Business card design for my company.
I would like the card's background colour to be black. You can also see our web site to get an idea of our brand. https://www.tmwhomecrafting.com.au/
- Name
- Email

```html
<!DOCTYPE html>
<html lang="en">
<head>
<meta charset="utf-8">
<title>TMW Home Crafting – Business Card</title>
<link rel="stylesheet" href="https://fonts.googleapis.com/css2?family=Figtree:wght@400;500;700;800&display=swap">
<style>
  :root {
    --backdrop: #1b1b1b;
    --card-light: #f2f2f2;
    --card-dark: #161616;
    --brand-green: #07944a;
    --brand-green-light: #1fa35c;
    --ink: #1e1e1e;
    --white: #ffffff;
  }
  * { margin: 0; padding: 0; box-sizing: border-box; }
  html, body {
    width: 1200px;
    height: 1059px;
    overflow: hidden;
    background: var(--backdrop);
    font-family: "Figtree", "Helvetica Neue", Arial, sans-serif;
  }
  .canvas { position: relative; width: 1200px; height: 1059px; }

  .card {
    position: absolute;
    border-radius: 18px;
    overflow: hidden;
  }

  /* Front */
  .card--front {
    left: 256px; top: 89px;
    width: 689px; height: 393px;
    background: var(--card-light);
  }
  .card__swoosh { position: absolute; inset: 0; width: 689px; height: 393px; }
  .holder__name {
    position: absolute; left: 25px; top: 42px;
    font-size: 31px; font-weight: 700; color: var(--brand-green);
    letter-spacing: 0.2px;
  }
  .holder__title {
    position: absolute; left: 25px; top: 81px;
    font-size: 17px; font-weight: 400; color: var(--ink); letter-spacing: 0.5px;
  }
  .holder__location {
    position: absolute; left: 25px; top: 177px;
    font-size: 17px; color: var(--ink); letter-spacing: 0.5px;
  }
  .contact-list {
    position: absolute; left: 25px; top: 270px;
    list-style: none;
  }
  .contact-list__item {
    display: flex; align-items: center; gap: 8px;
    height: 27.5px;
    font-size: 17px; color: var(--ink); letter-spacing: 0.4px;
  }
  .contact-list__icon { width: 16px; height: 16px; flex: none; }

  .brand-mark--front {
    position: absolute; left: 465px; top: 0; width: 224px; height: 393px;
    display: flex; align-items: center; justify-content: center;
    text-align: center;
    color: var(--white); font-weight: 800; font-size: 25px; line-height: 1.2;
    letter-spacing: 0.5px;
  }

  /* Back */
  .card--back {
    left: 253px; top: 546px;
    width: 695px; height: 396px;
    background: linear-gradient(120deg, var(--brand-green) 0%, var(--brand-green) 35%, var(--brand-green-light) 55%, var(--brand-green) 80%);
    display: flex; align-items: center; justify-content: center;
  }
  .brand-mark--back {
    color: var(--white); font-weight: 800; font-size: 52px; letter-spacing: 1px;
  }
</style>
</head>
<body>
<main class="canvas">

  <section class="card card--front" aria-label="Business card front">
    <svg class="card__swoosh" viewBox="0 0 689 393" aria-hidden="true">
      <path d="M482 0 C380 110 330 270 403 393 L689 393 L689 0 Z" fill="var(--card-dark)"/>
      <path d="M492 0 C392 112 346 272 418 393 L689 393 L689 0 Z" fill="var(--brand-green)"/>
      <path d="M532 0 C430 112 390 272 444 393 L689 393 L689 0 Z" fill="var(--card-dark)"/>
    </svg>

    <h1 class="holder__name">Liam Harcourt</h1>
    <p class="holder__title">General Manager</p>
    <p class="holder__location">Hobart, Tasmania, Australia</p>

    <ul class="contact-list">
      <li class="contact-list__item">
        <svg class="contact-list__icon" viewBox="0 0 16 16" aria-hidden="true">
          <path d="M2 6 C2 3 14 3 14 6 L12 7 L11 5.5 H5 L4 7 Z" fill="var(--brand-green)"/>
          <path d="M4 8 L5.5 6.5 H10.5 L12 8 V13 H4 Z" fill="var(--brand-green)"/>
        </svg>
        0400 123 456
      </li>
      <li class="contact-list__item">
        <svg class="contact-list__icon" viewBox="0 0 16 16" aria-hidden="true">
          <rect x="1.5" y="4" width="13" height="9" fill="var(--brand-green)"/>
          <path d="M1.5 4 L8 9 L14.5 4" fill="none" stroke="var(--card-light)" stroke-width="1.2"/>
        </svg>
        info@tmwhomecrafting.com.au
      </li>
      <li class="contact-list__item">
        <svg class="contact-list__icon" viewBox="0 0 16 16" aria-hidden="true">
          <circle cx="8" cy="8" r="6.5" fill="var(--brand-green)"/>
          <path d="M5 4 C7 5 6 7 8 8 C9 10 7 11 8 13" fill="none" stroke="var(--card-light)" stroke-width="1.2"/>
        </svg>
        www.tmwhomecrafting.com.au
      </li>
    </ul>

    <p class="brand-mark brand-mark--front">TMW<br>Home<br>Crafting</p>
  </section>

  <section class="card card--back" aria-label="Business card back">
    <p class="brand-mark brand-mark--back">TMW Home Crafting</p>
  </section>

</main>
</body>
</html>
```